CalmPeak Nurses' Manifesto

Design a manifesto to inspire and motivate nurses to work at minimum standards of excellence in their nursing practice.

The manifesto will become a feature of our website, at conferences, workshops and retreats. It will also be featured on other marketing tools.

Primary Market:
Nurses and/or other healthcare professionals (specifically Doctors, Occupational Therapists, Psychologists and Social Workers).

However the manifesto is equally applicable to all nurses and healthcare professionals from new graduates to very experienced senior clinicians, administration officers,managers and healthcare executive personnel.

Mainly females and primarily 35 to 65 years old, which suggests people in this target age group have extensive experience, but have become jaded'.

The purpose of our business is to assist healthcare professionals, primarily nurses, to maintain their enthusiasm and excellence in service provision, for their benefit as well as the benefit of the clients.

I have attached:
File 1: Copy Samples and examples: which has the copy for the manifesto, examples that appeal to us and our 3 attempts.
File 2: Our colour Spec Sheet, HOWEVER the colours are not necessary limited to these colours. These colours are not in the logo that will be on the manifesto. The colours on the logo attached can/or also be used.
File 3: Prototype logo. The final logo will be available within 3 to 4 days.

Industry/Entity Type

Healthcare

Requirements
Must have
• Must use the copy as per the attached file.

It should be contemporary, eye catching and motivational.

Should not have
• MUST BE EASY TO READ. Each line MUST be clearly defined from each other.

```html
<!DOCTYPE html>
<html lang="en">
<head>
<meta charset="utf-8">
<title>CalmPeak Nurses' Manifesto</title>
<link href="https://fonts.googleapis.com/css2?family=Anton&family=Arvo:wght@700&family=Oswald:wght@500;700&display=swap" rel="stylesheet">
<style>
  :root {
    --teal-deep: #2f4c49;
    --teal-mid: #4f6f6b;
    --teal-light: #8aa5a1;
    --ink-white: #f3f5f2;
    --leaf-green: #8dc63f;
    --card-white: #ffffff;
    --brand-teal: #2f8f8a;
  }
  html, body {
    margin: 0;
    padding: 0;
    overflow: hidden;
    background: var(--teal-deep);
  }
  .manifesto {
    position: relative;
    width: 810px;
    height: 1200px;
    overflow: hidden;
    font-family: "Anton", "Oswald", sans-serif;
    color: var(--ink-white);
  }
  .backdrop {
    position: absolute;
    inset: 0;
    background:
      radial-gradient(ellipse at 75% 25%, var(--teal-light) 0%, rgba(138,165,161,0) 50%),
      radial-gradient(ellipse at 40% 60%, rgba(127,156,152,0.6) 0%, rgba(127,156,152,0) 55%),
      linear-gradient(160deg, var(--teal-mid) 0%, var(--teal-deep) 100%);
  }
  .line {
    position: absolute;
    margin: 0;
    white-space: nowrap;
    line-height: 0.95;
    text-transform: uppercase;
    font-weight: 400;
    transform-origin: 0 0;
    transform: scaleX(var(--sx, 1));
  }
  .display { font-family: "Anton", sans-serif; }
  .caption { font-family: "Oswald", sans-serif; font-weight: 700; }
  .slab { font-family: "Arvo", serif; font-weight: 700; }
  .accent { color: var(--leaf-green); }
  .up { transform: rotate(-90deg) scaleX(var(--sx, 1)); }
  .down { transform: rotate(90deg) scaleX(var(--sx, 1)); }
  .title { text-transform: none; }
  .stack { line-height: 52px; }

  .brand-card {
    position: absolute;
    left: 547px; top: 1035px;
    width: 263px; height: 165px;
    background: var(--card-white);
    border-radius: 24px 0 0 0;
    display: flex;
    align-items: center;
    justify-content: center;
    gap: 14px;
  }
  .brand-dot {
    width: 44px; height: 44px;
    border-radius: 50%;
    background: var(--brand-teal);
    flex: none;
  }
  .brand-name {
    font-family: "Oswald", sans-serif;
    font-weight: 500;
    color: var(--brand-teal);
    font-size: 28px;
    line-height: 1.05;
  }
</style>
</head>
<body>
<main class="manifesto">
  <div class="backdrop" role="img" aria-label="Soft dark teal cloudy background"></div>

  <h1 class="line display accent title" style="left:108px;top:6px;font-size:48px;--sx:1.72;">Nurses' Manifesto</h1>

  <p class="line caption" style="left:30px;top:66px;font-size:32px;--sx:1.23;">Nurse with open hands, hearts and minds</p>
  <p class="line display" style="left:30px;top:104px;font-size:60px;--sx:0.94;">Only follow exceptional leaders</p>

  <p class="line display accent" style="left:30px;top:174px;font-size:108px;--sx:0.91;">Always</p>
  <p class="line caption" style="left:327px;top:181px;font-size:28px;--sx:0.81;">Lead with purpose passion and commitment</p>
  <p class="line display" style="left:327px;top:216px;font-size:40px;--sx:1.12;">Be solution focussed</p>

  <p class="line display down" style="left:787px;top:203px;font-size:75px;--sx:0.82;">Seek success firstly from within</p>

  <p class="line display" style="left:30px;top:271px;font-size:86px;--sx:1.05;">You are</p>
  <p class="line display" style="left:27px;top:364px;font-size:88px;--sx:1.31;">Unique</p>

  <p class="line display up" style="left:333px;top:607px;font-size:42px;line-height:1.05;--sx:1.52;">Revel in your<br>individuality</p>

  <p class="line display accent" style="left:427px;top:270px;font-size:105px;--sx:1.14;">Trust</p>
  <p class="line caption" style="left:432px;top:387px;font-size:36px;">Your knowledge</p>
  <p class="line caption" style="left:432px;top:432px;font-size:36px;--sx:1.03;">and seek advice</p>

  <p class="line display up" style="left:32px;top:607px;font-size:57px;--sx:0.91;">Always</p>
  <p class="line display" style="left:97px;top:460px;font-size:42px;--sx:1.03;">Do the right</p>
  <p class="line display" style="left:97px;top:508px;font-size:75px;--sx:1.28;">Thing</p>
  <p class="line caption" style="left:97px;top:572px;font-size:30px;--sx:0.84;">Without exception</p>

  <p class="line display" style="left:438px;top:484px;font-size:108px;--sx:1.33;">Only</p>
  <p class="line caption" style="left:435px;top:579px;font-size:37px;--sx:0.74;">Exceptional leaders</p>

  <p class="line display accent" style="left:27px;top:612px;font-size:92px;--sx:0.93;">Celebrate</p>
  <p class="line caption" style="left:27px;top:700px;font-size:35px;--sx:0.93;">Of Australian culture</p>

  <p class="line caption" style="left:387px;top:625px;font-size:32px;--sx:0.96;">Respect and value the</p>
  <p class="line display" style="left:387px;top:660px;font-size:110px;--sx:0.79;">Diversity</p>
  <p class="line slab accent" style="left:387px;top:754px;font-size:50px;--sx:1.08;">Champion</p>

  <p class="line display" style="left:27px;top:760px;font-size:60px;--sx:1.38;">Support</p>
  <p class="line caption" style="left:27px;top:818px;font-size:47px;--sx:0.74;">Your colleagues</p>
  <p class="line display down" style="left:357px;top:762px;font-size:53px;--sx:1.38;">And</p>

  <p class="line caption" style="left:378px;top:804px;font-size:30px;letter-spacing:19px;">Their</p>
  <p class="line caption" style="left:378px;top:829px;font-size:40px;--sx:0.97;">Purpose</p>
  <p class="line display" style="left:537px;top:805px;font-size:52px;--sx:1.09;">Choose</p>
  <p class="line caption" style="left:537px;top:850px;font-size:20px;--sx:0.8;">Your thoughts wisely</p>

  <p class="line display accent" style="left:27px;top:874px;font-size:100px;--sx:0.96;">Learn</p>
  <p class="line display" style="left:252px;top:875px;font-size:52px;--sx:1.01;">Something</p>
  <p class="line caption" style="left:252px;top:927px;font-size:40px;--sx:0.93;">New each day</p>

  <p class="line display up" style="left:483px;top:1035px;font-size:52px;--sx:0.82;">Reality</p>
  <p class="line display" style="left:540px;top:878px;font-size:98px;--sx:0.98;">They</p>
  <p class="line display" style="left:547px;top:965px;font-size:68px;--sx:0.89;">Create</p>

  <p class="line caption stack" style="left:27px;top:964px;font-size:40px;--sx:0.95;">Be<br>a<br>lifelong<br>learner</p>
  <p class="line display" style="left:112px;top:972px;font-size:114px;--sx:1.05;">Deliver</p>
  <p class="line display down" style="left:517px;top:1035px;font-size:55px;--sx:1.07;">Dream</p>
  <p class="line caption" style="left:187px;top:1077px;font-size:40px;">Care skillfully</p>
  <p class="line display accent" style="left:187px;top:1121px;font-size:62px;--sx:1.25;">Live your</p>

  <div class="brand-card">
    <span class="brand-dot"></span>
    <span class="brand-name">CalmPeak<br>For Nurses</span>
  </div>
</main>
</body>
</html>
```